Redesign of business card for Cedar Ridge Mechanical

We are looking for a new design for our business cards for Cedar Ridge Mechanical. We are a plumbing & HVAC construction company, operating on the West Coast of Canada and USA. Logo attached.
Industry/Entity Type
Construction - Plumbing & HVAC
Contact Information for Business Card
Name, address, phone numbers, email, website address
Look and feel
Each slider illustrates characteristics of the customer's brand and the style your logo design should communicate.

```html
<!DOCTYPE html>
<html lang="en">
<head>
<meta charset="utf-8">
<title>Cedar Ridge Mechanical – Business Card</title>
<link rel="stylesheet" href="https://fonts.googleapis.com/css2?family=Montserrat:wght@400;500;700&display=swap">
<style>
  :root {
    --backdrop: #1b1b1b;
    --card-white: #ffffff;
    --card-black: #1e1e1e;
    --accent-grey: #8a8a8a;
    --text-dark: #151515;
    --text-muted: #6f6f6f;
  }
  html, body {
    margin: 0;
    width: 1200px;
    height: 963px;
    overflow: hidden;
    background: var(--backdrop);
  }
  .canvas {
    position: relative;
    width: 1200px;
    height: 963px;
    display: flex;
    align-items: center;
    justify-content: center;
    font-family: "Montserrat", sans-serif;
  }
  .card {
    position: relative;
    width: 900px;
    height: 514px;
    border-radius: 36px;
    overflow: hidden;
    background: var(--card-white);
    box-shadow: 0 20px 50px rgba(0,0,0,0.6);
  }
  .card-shapes {
    position: absolute;
    inset: 0;
  }
  .contact-block {
    position: absolute;
    left: 62px;
    top: 62px;
    color: var(--text-muted);
  }
  .person-name {
    margin: 0;
    font-size: 30px;
    font-weight: 700;
    letter-spacing: 1px;
    color: var(--text-dark);
    line-height: 1.1;
  }
  .person-name .surname { color: var(--accent-grey); }
  .person-role {
    margin: 2px 0 0;
    font-size: 22px;
    font-weight: 400;
  }
  .address {
    margin: 38px 0 0;
    font-size: 22px;
    line-height: 1.2;
  }
  .contact-list {
    list-style: none;
    margin: 34px 0 0;
    padding: 0;
    font-size: 22px;
    line-height: 1.35;
  }
  .contact-list li {
    display: flex;
    align-items: center;
    gap: 10px;
  }
  .contact-list .web { color: var(--text-dark); }
  .contact-list .web b { font-weight: 700; }
  .contact-icon { width: 16px; height: 16px; fill: var(--text-dark); flex: none; }
  .brand-mark {
    position: absolute;
    left: 555px;
    top: 232px;
    display: flex;
    align-items: center;
    gap: 14px;
    color: var(--card-white);
    font-size: 24px;
    font-weight: 500;
    letter-spacing: 1px;
    text-transform: uppercase;
    line-height: 1.15;
  }
  .brand-square {
    width: 34px;
    height: 34px;
    border: 4px solid var(--card-white);
    border-radius: 4px;
    flex: none;
  }
</style>
</head>
<body>
<main class="canvas">
  <article class="card">
    <svg class="card-shapes" viewBox="0 0 900 514" width="900" height="514" aria-hidden="true">
      <path fill="var(--accent-grey)" d="M592,0 C500,0 495,120 448,250 C400,380 380,514 305,514 L900,514 L900,0 Z"/>
      <path fill="var(--card-black)" d="M616,0 C530,0 522,120 476,250 C430,380 410,514 335,514 L900,514 L900,0 Z"/>
    </svg>

    <section class="contact-block">
      <h1 class="person-name">JONATHAN <span class="surname">SMITH</span></h1>
      <p class="person-role">Manager</p>
      <p class="address">Your address, city<br>state, ZIP 0000</p>
      <ul class="contact-list">
        <li>
          <svg class="contact-icon" viewBox="0 0 16 16"><path d="M3 1h3l1.5 4-2 1.2a9 9 0 0 0 4.3 4.3L11 8.5l4 1.5v3a2 2 0 0 1-2 2A12 12 0 0 1 1 3a2 2 0 0 1 2-2z"/></svg>
          123-456-2100
        </li>
        <li>
          <svg class="contact-icon" viewBox="0 0 16 16"><path d="M1 3h14v10H1z M2 4l6 5 6-5" stroke="#fff" stroke-width="1"/></svg>
          youremail@mailbox.com
        </li>
        <li class="web">
          <svg class="contact-icon" viewBox="0 0 16 16"><circle cx="8" cy="8" r="7"/><path d="M1 8h14M8 1c3 3 3 11 0 14M8 1c-3 3-3 11 0 14" stroke="#fff" stroke-width="1" fill="none"/></svg>
          <span>www.<b>yourwebsite</b>.com</span>
        </li>
      </ul>
    </section>

    <div class="brand-mark">
      <span class="brand-square"></span>
      <span class="brand-name">Cedar Ridge<br>Mechanical</span>
    </div>
  </article>
</main>
</body>
</html>
```